Thornvale Group needs a business card design

We need a new business card design using the logo recently selected in a logo competition on Pixel Bazaar. Our business is a consultancy specializing in aviation and energy and the winning business card design will promote an image of precision and professionalism with creativity.

Please use the logo with the name on the front of the card and use a complementary font. Make the back white with either the light grey or dark grey logo.

Target Market(s)

Senior finance and legal leaders at aviation and energy companies

Industry/Entity Type

Management Consulting

Contact Information for Business Card

Peter Castrell
President
Thornvale Group

www.thornvalegroup.example

(555) 204-6391
pc@thornvalegroup.example

Requirements
Must have
• Professional font that goes well with the logo font

```html
<!DOCTYPE html>
<html lang="en">
<head>
<meta charset="utf-8">
<title>Thornvale Group — Business Card</title>
<link href="https://fonts.googleapis.com/css2?family=Open+Sans:wght@400;600;700&display=swap" rel="stylesheet">
<style>
  :root {
    --backdrop: #e9e7e4;
    --card-white: #ffffff;
    --brand-blue: #1d4e85;
    --brand-blue-deep: #143a66;
    --brand-blue-light: #3f78b5;
    --text-grey: #8a8f96;
    --slate-top: #6f7479;
    --slate-bottom: #34383c;
    --contact-white: #ffffff;
  }
  * { margin: 0; padding: 0; box-sizing: border-box; }
  html, body {
    width: 1200px; height: 913px; overflow: hidden;
    background: var(--backdrop);
    font-family: "Open Sans", Arial, sans-serif;
  }
  .canvas { position: relative; width: 1200px; height: 913px; }

  .card {
    position: absolute;
    width: 560px; height: 320px;
    border-radius: 18px;
    overflow: hidden;
    box-shadow: 0 10px 28px rgba(0,0,0,0.18);
  }

  /* Front */
  .card-front { left: 70px; top: 80px; background: var(--card-white); }
  .card-front .wave { position: absolute; inset: 0; width: 100%; height: 100%; }

  .holder { position: absolute; right: 34px; top: 28px; text-align: right; }
  .holder-name { font-size: 24px; font-weight: 700; color: var(--brand-blue); line-height: 1.1; }
  .holder-title { font-size: 14px; font-weight: 400; color: var(--text-grey); margin-top: 2px; }

  .wordmark {
    position: absolute;
    display: flex; align-items: center; gap: 12px;
    font-weight: 600; color: var(--brand-blue);
    letter-spacing: 0.06em;
  }
  .card-front .wordmark { left: 40px; top: 138px; font-size: 30px; }
  .wordmark-dot { width: 14px; height: 14px; background: currentColor; flex: none; }

  .contact {
    position: absolute; right: 34px; top: 178px;
    list-style: none; text-align: right;
    color: var(--contact-white); font-size: 14px; line-height: 1.75;
  }
  .contact li { display: flex; justify-content: flex-end; align-items: center; gap: 8px; }
  .contact svg { width: 13px; height: 13px; flex: none; }

  /* Back */
  .card-back {
    left: 570px; top: 500px;
    background: linear-gradient(160deg, var(--slate-top) 0%, var(--slate-bottom) 100%);
  }
  .card-back .wordmark {
    left: 50%; top: 50%; transform: translate(-50%, -50%);
    font-size: 38px; color: var(--brand-blue-light); white-space: nowrap;
  }
</style>
</head>
<body>
<main class="canvas">

  <section class="card card-front" aria-label="Business card front">
    <svg class="wave" viewBox="0 0 560 320" preserveAspectRatio="none" aria-hidden="true">
      <path d="M170 320 C 270 318, 300 190, 400 158 C 460 138, 520 140, 560 150 L 560 320 Z" fill="var(--brand-blue)"/>
      <path d="M150 320 C 250 312, 290 178, 392 148 C 455 130, 515 132, 560 142 L 560 150 C 520 140, 460 138, 400 158 C 300 190, 270 318, 170 320 Z" fill="var(--brand-blue-light)" opacity="0.55"/>
      <path d="M330 320 C 400 300, 440 250, 560 235 L 560 320 Z" fill="var(--brand-blue-deep)" opacity="0.35"/>
    </svg>

    <div class="holder">
      <p class="holder-name">Peter Castrell</p>
      <p class="holder-title">President</p>
    </div>

    <div class="wordmark"><span class="wordmark-dot"></span>Thornvale Group</div>

    <ul class="contact">
      <li>(555) 204-6391
        <svg viewBox="0 0 16 16" aria-hidden="true"><path fill="currentColor" d="M3.6 1.5l2.3 2.6-1.3 1.7a9 9 0 0 0 5.6 5.6l1.7-1.3 2.6 2.3-1.5 2.1C7.5 14.3 1.7 8.5 1.5 3z"/></svg>
      </li>
      <li>pc@thornvalegroup.example
        <svg viewBox="0 0 16 16" aria-hidden="true"><rect x="1.5" y="3.5" width="13" height="9" rx="1" fill="none" stroke="currentColor" stroke-width="1.5"/><path d="M2 4.5l6 4.5 6-4.5" fill="none" stroke="currentColor" stroke-width="1.5"/></svg>
      </li>
      <li>www.thornvalegroup.example
        <svg viewBox="0 0 16 16" aria-hidden="true"><circle cx="8" cy="8" r="6.5" fill="none" stroke="currentColor" stroke-width="1.5"/><path d="M1.5 8h13M8 1.5c-3 3.5-3 9.5 0 13M8 1.5c3 3.5 3 9.5 0 13" fill="none" stroke="currentColor" stroke-width="1.2"/></svg>
      </li>
    </ul>
  </section>

  <section class="card card-back" aria-label="Business card back">
    <div class="wordmark"><span class="wordmark-dot"></span>Thornvale Group</div>
  </section>

</main>
</body>
</html>
```